Velmora Trading Company product labels (5"wide x7" high (12,5 cm x 17,5 cm))

We need a vertical product label that will go on the Gold stand up bags for our Kratom powder. We are looking for professional looking and attractive label design that will capture the attention of consumers. Our products should stand out when sitting on a shelf next to our competitors. We want one label which we will be able to use for all the different Kratom Powders we have.The product label will be used for several different varieties of Kratom so there will need to be an area available for the varieties name such as "RED BORNEO" or "GREEN MAENG DA" etc., which we will apply a small label as needed.
The label dimensions should be 5" wide x 7" high (12,5 cm wide x 17,5 cm high).
Please review the "must haves" section, and please try and include the "nice to haves" if possible.

Target Market(s)

Health minded consumers who love natural products, and are looking for plant based alternatives to harmful synthetic products.

Industry/Entity Type

Supplement

Colors

Designer to choose colors to be used in the design.

Requirements
Must have
• Product labels must include:
• 1) Company logo (find in the attachments)
• 2) Product information (find in the attachments)
• 3) Product title - Premium Kratom Powder
• 4) Weight indication - 250 grams
• 5) Barcode
• 6) Icon that says - 100% pure (or "100% natural")
Nice to have
• Indonesian jungle theme.
• Our packaging is gold metallic stand up bag, so the colors should be complimenting the bag.
Should not have
• labels or part of the labels taken from other Kratom companies. The design should be unique.

```html
<!DOCTYPE html>
<html lang="en">
<head>
<meta charset="utf-8">
<title>Velmora Trading Company – Premium Kratom Powder Labels</title>
<link href="https://fonts.googleapis.com/css2?family=Montserrat:wght@500;600;700;800&family=Open+Sans:wght@400;600&display=swap" rel="stylesheet">
<style>
  :root {
    --canvas-bg: #e9e6df;
    --jungle-deep: #1f6b2c;
    --jungle-mid: #3f9a3a;
    --jungle-light: #8cc63f;
    --title-yellow: #ece77c;
    --badge-yellow: #e6e36a;
    --badge-ink: #2f6a23;
    --label-white: #ffffff;
    --gold-light: #f3ecd0;
    --gold-mid: #d9cc98;
    --gold-deep: #b9a864;
    --back-ink: #3d3a2c;
    --barcode-block: #111111;
    --weight-chip: #7fb53c;
  }
  * { box-sizing: border-box; margin: 0; padding: 0; }
  html, body { width: 1200px; height: 823px; overflow: hidden; }
  body {
    background: var(--canvas-bg);
    font-family: "Open Sans", Arial, sans-serif;
    position: relative;
  }
  .label {
    position: absolute;
    top: 82px;
    width: 470px;
    height: 658px;
    border-radius: 6px;
    overflow: hidden;
    box-shadow: 0 6px 20px rgba(0,0,0,.15);
  }
  .label--front { left: 110px; }
  .label--back { left: 620px; }

  /* Front */
  .jungle-art {
    position: absolute; inset: 0;
    background:
      radial-gradient(ellipse at 50% 88%, var(--jungle-light) 0%, rgba(140,198,63,0) 45%),
      linear-gradient(180deg, var(--jungle-mid) 0%, var(--jungle-light) 40%, var(--jungle-mid) 70%, var(--jungle-deep) 100%);
  }
  .brand {
    position: absolute; top: 100px; left: 0; right: 0;
    display: flex; flex-direction: column; align-items: center;
  }
  .brand__circle {
    width: 128px; height: 128px; border-radius: 50%;
    background: var(--label-white);
    display: flex; align-items: center; justify-content: center;
    text-align: center;
  }
  .brand__name {
    font-family: "Montserrat", Arial, sans-serif;
    font-weight: 700;
    font-size: 15px;
    line-height: 1.2;
    color: var(--jungle-deep);
    letter-spacing: .5px;
    text-transform: uppercase;
  }
  /* Empty area kept free for the applied variety sticker */
  .variety-slot {
    position: absolute; top: 236px; left: 95px; right: 95px; height: 40px;
  }
  .product-title {
    position: absolute; top: 282px; left: 0; right: 0;
    text-align: center;
    font-family: "Montserrat", Arial, sans-serif;
  }
  .product-title__main {
    display: block;
    font-weight: 800; font-size: 56px; line-height: 1.05; letter-spacing: 1px;
    color: var(--title-yellow);
  }
  .product-title__sub {
    display: block;
    font-weight: 600; font-size: 24px; letter-spacing: 1px;
    color: var(--label-white);
    margin-top: 2px;
  }
  .natural-badge {
    position: absolute; top: 418px; left: 0; right: 0;
    display: flex; flex-direction: column; align-items: center;
    font-family: "Montserrat", Arial, sans-serif;
  }
  .natural-badge__percent {
    display: flex; align-items: center; gap: 6px;
    font-weight: 800; font-size: 38px; color: var(--badge-yellow);
  }
  .natural-badge__heart { width: 20px; height: 18px; }
  .natural-badge__word {
    margin-top: 2px;
    background: var(--badge-yellow);
    color: var(--badge-ink);
    font-weight: 800; font-size: 34px;
    padding: 0 22px 4px;
    border-radius: 4px;
    transform: rotate(-3deg);
  }
  .net-weight {
    position: absolute; bottom: 52px; left: 50%;
    transform: translateX(-50%);
    background: var(--weight-chip);
    color: var(--title-yellow);
    font-family: "Montserrat", Arial, sans-serif;
    font-weight: 700; font-size: 16px;
    padding: 4px 16px; border-radius: 6px;
  }

  /* Back */
  .label--back {
    background: linear-gradient(160deg, var(--gold-light) 0%, var(--gold-mid) 60%, var(--gold-deep) 100%);
    color: var(--back-ink);
    text-align: center;
  }
  .foliage-art {
    position: absolute; left: 0; right: 0; bottom: 0; height: 150px;
    background: linear-gradient(180deg, rgba(185,168,100,0) 0%, rgba(185,168,100,.55) 100%);
  }
  .label--back .brand { top: 110px; }
  .label--back .brand__circle { width: 120px; height: 120px; background: transparent; border: 3px solid var(--back-ink); }
  .label--back .brand__name { color: var(--back-ink); font-size: 14px; }
  .back-copy {
    position: absolute; top: 272px; left: 48px; right: 48px;
  }
  .back-copy__ingredients,
  .back-copy__warning {
    font-size: 13.5px; line-height: 1.4;
  }
  .back-copy__heading { text-transform: uppercase; }
  .back-copy__warning { margin-top: 22px; text-transform: uppercase; }
  .back-copy__disclaimer {
    margin-top: 20px;
    font-size: 9.5px; line-height: 1.45;
  }
  .back-copy__distributor {
    margin-top: 12px;
    font-size: 11.5px; line-height: 1.5; text-transform: uppercase;
  }
  .barcode-area {
    position: absolute; top: 563px; left: 50%;
    transform: translateX(-50%);
    width: 166px; height: 52px;
    background: var(--barcode-block);
    color: var(--label-white);
    font-size: 10px; font-weight: 600; letter-spacing: .5px;
    display: flex; align-items: center; justify-content: center;
  }
</style>
</head>
<body>

  <section class="label label--front">
    <div class="jungle-art" role="img" aria-label="Illustrated Indonesian jungle with trees, vines and leafy undergrowth in greens"></div>

    <div class="brand">
      <div class="brand__circle">
        <span class="brand__name">Velmora<br>Trading<br>Company</span>
      </div>
    </div>

    <div class="variety-slot" aria-hidden="true"></div>

    <h1 class="product-title">
      <span class="product-title__main">PREMIUM</span>
      <span class="product-title__sub">KRATOM POWDER</span>
    </h1>

    <div class="natural-badge">
      <div class="natural-badge__percent">
        <svg class="natural-badge__heart" viewBox="0 0 20 18" aria-hidden="true"><path d="M10 17 C2 11 0 8 0 5 A5 5 0 0 1 10 3 A5 5 0 0 1 20 5 C20 8 18 11 10 17Z" fill="var(--badge-yellow)"/></svg>
        100%
        <svg class="natural-badge__heart" viewBox="0 0 20 18" aria-hidden="true"><path d="M10 17 C2 11 0 8 0 5 A5 5 0 0 1 10 3 A5 5 0 0 1 20 5 C20 8 18 11 10 17Z" fill="var(--badge-yellow)"/></svg>
      </div>
      <div class="natural-badge__word">natural</div>
    </div>

    <div class="net-weight">250 grams</div>
  </section>

  <section class="label label--back">
    <div class="foliage-art" role="img" aria-label="Faint gold jungle foliage along the lower edge"></div>

    <div class="brand">
      <div class="brand__circle">
        <span class="brand__name">Velmora<br>Trading<br>Company</span>
      </div>
    </div>

    <div class="back-copy">
      <p class="back-copy__ingredients">
        <span class="back-copy__heading">Ingredients:</span><br>
        100% natural Mitragyna Speciosa leaf powder.
      </p>
      <p class="back-copy__warning">
        Not for sale to minors.<br>
        Must be 18 years or older to purchase.<br>
        Keep out of reach of children.
      </p>
      <p class="back-copy__disclaimer">
        Do not use any botanicals without a physician's consent, if you are a minor, pregnant, nursing or taking MAOIs. These statements have not been evaluated by the FDA and is not intended to diagnose, treat, cure or prevent any disease. Caution while driving or using heavy machinery.
      </p>
      <p class="back-copy__distributor">
        Distributed by:<br>
        Velmora Trading Company Cedarholt,<br>
        FL 32999
      </p>
    </div>

    <div class="barcode-area">BAR CODE</div>
  </section>

</body>
</html>
```